Postcard Mail Out - Dwight

We are a real estate company. We need a post card to mail out to potential clients to try and sale their land. We will attached a couple of post cards that we like but we do not want to copy them completely. We do need to put the Equal Housing Opportunity and the Realtor logos with a disclosure saying not intended to solicit currently listed properties. The image below is what we had started working on. We would like to include something about farm land, timber, maybe a pond, something along those lines. The PDF Files attached are a flyer that was mailed out by another company that we do not want to copy completely. Attached also will be our company's Logo.

Requirements
Must have
• We do need to put the Equal Housing Opportunity and the Realtor logos with a disclosure saying not intended to solicit currently listed properties.<br/><br/>At Cobb Harlow Summit Realty, we are blessed to have one of the very best Rural Land Specialists available. Dwight has years of experience promoting and selling rural land properties. Dwight has earned the trust of many landowners, as he is so PASSIONATE in all regards to rural land, farms and ranches. He has made a wide range of landowners very happy throughout his years in Real Estate. Call him today and show him your property, and he will provide you with a free analysis and strategy to maximize the return on your property.
Nice to have
• A picture of Dwight has been added to use on the back of the post card with his phone and number. It would be nice to have a east Texas scenery picture behind him instead of an office.<br/><br/>Please include front and back of post card in your submission.
Should not have
• Should not have Marcus Thorne's information on the postcard. That post card was just to show what we was wanting. The agent we want listed is Dwight Fenwick and his phone number is (555)412-3086.

```html
<!DOCTYPE html>
<html lang="en">
<head>
<meta charset="utf-8">
<title>Postcard Mail Out – Dwight Fenwick</title>
<link href="https://fonts.googleapis.com/css2?family=Open+Sans:wght@400;600;700;800&family=Cinzel:wght@600;700&family=Noto+Serif:wght@700&display=swap" rel="stylesheet">
<style>
  :root{
    --bg:#d6d6d6;
    --brand:#1f6aa8;
    --brand-dark:#14507f;
    --navy:#163a6b;
    --ink:#1b3f6e;
    --paper:#f3f3f3;
    --white:#ffffff;
    --line:#2b2b9a;
  }
  *{box-sizing:border-box;margin:0;padding:0}
  html,body{width:1200px;height:696px;overflow:hidden;background:var(--bg)}
  .canvas{position:relative;width:1200px;height:696px;background:var(--bg)}
  .card{position:absolute;width:540px;height:360px;overflow:hidden;box-shadow:0 4px 10px rgba(0,0,0,.25)}

  /* ---------- back ---------- */
  .card-back{left:40px;top:168px;background:var(--paper)}
  .back-scenery{position:absolute;inset:0;background:linear-gradient(160deg,#f7f7f7 0%,#e4e4e4 45%,#cfcfcf 100%)}
  .back-shapes{position:absolute;inset:0}
  .brand{position:absolute;left:40px;top:30px;display:flex;align-items:center;gap:10px}
  .brand-dot{width:30px;height:30px;border-radius:50%;background:var(--brand-dark)}
  .brand-name{font-family:"Noto Serif",serif;font-weight:700;font-size:19px;line-height:1.05;color:var(--brand-dark)}
  .tagline{position:absolute;left:34px;top:98px;font-family:"Cinzel",serif;font-weight:700;color:var(--navy);font-size:12.5px;letter-spacing:.3px;white-space:nowrap}
  .tagline.eho{top:118px;color:var(--brand);font-size:12px}
  .agent-photo{position:absolute;left:50px;top:146px;width:150px;height:100px;border-radius:12px;border:3px solid var(--white);
    background:linear-gradient(180deg,#3b9be0 0%,#7fc3ef 45%,#7aa64b 75%,#d9cfb5 100%)}
  .agent-name{position:absolute;left:60px;top:254px;font-family:"Open Sans",sans-serif;font-weight:700;font-size:20px;color:var(--navy);white-space:nowrap}
  .agent-phone{position:absolute;left:26px;top:280px;font-family:"Open Sans",sans-serif;font-weight:800;font-size:29px;line-height:1.2;color:var(--brand);white-space:nowrap}
  .contact{position:absolute;left:10px;bottom:7px;width:280px;font-family:"Open Sans",sans-serif;font-size:7px;font-weight:600;color:var(--white);line-height:1.55}
  .contact .row{display:flex;align-items:center;gap:4px;white-space:nowrap}
  .contact .row:first-child{padding-left:40px}
  .contact svg{width:8px;height:8px;flex:none}
  .thumb{position:absolute;width:54px;height:54px;border-radius:50%;border:4px solid var(--white);box-shadow:0 1px 3px rgba(0,0,0,.3)}
  .thumb.farm{left:364px;top:26px;background:linear-gradient(180deg,#5aa3e6 0%,#8fc8f0 45%,#5f9c3a 70%,#b83a2e 100%)}
  .thumb.lane{left:334px;top:98px;background:linear-gradient(180deg,#4d9ee8 0%,#9dd0f3 45%,#4b8a35 80%)}
  .thumb.field{left:306px;top:168px;background:linear-gradient(180deg,#3d7fd6 0%,#8fb9e8 40%,#3f7c2c 75%)}
  .thumb.estate{left:278px;top:238px;background:linear-gradient(180deg,#1b2a55 0%,#3d5e9c 45%,#d8b06a 70%,#5aa0c8 100%)}
  .stamp{position:absolute;left:448px;top:38px;width:76px;height:68px;border:1.5px solid var(--line)}

  /* ---------- front ---------- */
  .card-front{left:620px;top:168px;background:var(--white)}
  .strips{position:absolute;inset:0;display:flex;gap:4px;background:var(--white)}
  .strip{flex:1;position:relative}
  .strip.rail{background:linear-gradient(180deg,#9fbfe0 0%,#8fa87a 35%,#b7a57a 70%,#9b8f6a 100%)}
  .strip.silos{background:linear-gradient(180deg,#1f5fc6 0%,#5aa0e6 30%,#c9ced4 55%,#b8a586 100%)}
  .strip.forest{background:linear-gradient(180deg,#6d7c93 0%,#b7872e 30%,#6b8a2a 55%,#3f7a2e 100%)}
  .strip.pasture{background:linear-gradient(180deg,#a9e1f2 0%,#b9a98a 35%,#a99b82 65%,#b8a98d 100%)}
  .strip.orchard{background:linear-gradient(180deg,#6f96d6 0%,#a09a86 25%,#8b6a3e 55%,#6d5a30 100%)}
  .sky-band{position:absolute;left:0;right:0;top:0;height:42px;background:rgba(255,255,255,.18)}
  .headline-band{position:absolute;left:0;right:0;top:82px;height:74px;background:rgba(255,255,255,.55)}
  .headline{position:absolute;left:0;right:0;top:86px;text-align:center;font-family:"Open Sans",sans-serif;font-weight:800;font-size:50px;line-height:1.3;color:var(--white);
    -webkit-text-stroke:2.5px var(--brand-dark);paint-order:stroke fill;letter-spacing:.5px}
  .about{position:absolute;left:16px;right:16px;top:222px;padding:8px 12px;border-radius:6px;background:rgba(255,255,255,.85);
    font-family:"Open Sans",sans-serif;font-size:8.2px;line-height:1.45;color:var(--ink)}
  .about strong{font-weight:700;color:var(--brand-dark)}
  .front-footer{position:absolute;left:0;right:0;bottom:0;height:30px;background:var(--brand);display:flex;align-items:center;gap:8px;padding:0 14px}
  .badge{width:18px;height:18px;border:1.5px solid var(--white);flex:none}
  .disclosure{margin-left:6px;font-family:"Open Sans",sans-serif;font-size:8px;font-weight:600;color:var(--white);white-space:nowrap}
</style>
</head>
<body>
<div class="canvas">

  <section class="card card-back" aria-label="Postcard back">
    <div class="back-scenery" role="img" aria-label="Faded photo of a stone country house"></div>
    <svg class="back-shapes" width="540" height="360" viewBox="0 0 540 360">
      <polygon points="404,0 416,0 276,360 264,360" fill="var(--brand)"/>
      <polygon points="0,322 290,322 274,360 0,360" fill="var(--brand)"/>
      <line x1="340" y1="180" x2="512" y2="188" stroke="var(--line)" stroke-width="1"/>
      <line x1="330" y1="212" x2="512" y2="222" stroke="var(--line)" stroke-width="1"/>
      <line x1="318" y1="244" x2="512" y2="256" stroke="var(--line)" stroke-width="1"/>
      <line x1="306" y1="276" x2="512" y2="290" stroke="var(--line)" stroke-width="1"/>
    </svg>

    <div class="brand">
      <span class="brand-dot"></span>
      <span class="brand-name">Cobb Harlow Summit<br>Realty</span>
    </div>
    <p class="tagline">Specializing in Rural Land Sales</p>
    <p class="tagline eho">Equal Housing Opportunity</p>

    <div class="agent-photo" role="img" aria-label="Dwight on the phone on an East Texas country lane"></div>
    <p class="agent-name">Dwight Fenwick</p>
    <p class="agent-phone">(555)412-3086</p>

    <div class="contact">
      <div class="row">
        <svg viewBox="0 0 10 10"><path d="M2 1l2 2-1 1.5a6 6 0 0 0 2.5 2.5L7 6l2 2-1.5 1.5C4 9 1 6 .5 2.5z" fill="#fff"/></svg>
        (555)412-3086 &nbsp; www.summitlandco.com
      </div>
      <div class="row">
        <svg viewBox="0 0 10 10"><path d="M5 .5a3 3 0 0 1 3 3c0 2.3-3 6-3 6s-3-3.7-3-6a3 3 0 0 1 3-3z" fill="#fff"/><circle cx="5" cy="3.5" r="1" fill="var(--brand)"/></svg>
        Pine Hollow, TX 75000, 48 W Oak St. Pine Hollow, TX 75000. Directions.
      </div>
    </div>

    <div class="thumb farm" role="img" aria-label="Red barn on green farmland"></div>
    <div class="thumb lane" role="img" aria-label="Country lane through trees"></div>
    <div class="thumb field" role="img" aria-label="Crop field with farmhouse"></div>
    <div class="thumb estate" role="img" aria-label="Lit house with pond at dusk"></div>

    <div class="stamp"></div>
  </section>

  <section class="card card-front" aria-label="Postcard front">
    <div class="strips">
      <div class="strip rail" role="img" aria-label="Aerial view of a train on rural tracks"></div>
      <div class="strip silos" role="img" aria-label="Grain silos on farm land"></div>
      <div class="strip forest" role="img" aria-label="Autumn timber land with farmhouse and pond"></div>
      <div class="strip pasture" role="img" aria-label="Cattle grazing on pasture"></div>
      <div class="strip orchard" role="img" aria-label="Hillside orchard rows"></div>
    </div>
    <div class="sky-band"></div>
    <div class="headline-band"></div>
    <h1 class="headline">Land For Sale?</h1>

    <p class="about">At <strong>Cobb Harlow Summit Realty</strong>, we are blessed to have one of the very best Rural Land Specialists available. Dwight has years of experience promoting and selling rural land properties. Dwight has earned the trust of many landowners, as he is so <strong>PASSIONATE</strong> in all regards to rural land, farms and ranches. He has made a wide range of landowners very happy throughout his years in Real Estate. Call him today and show him your property, and he will provide you with a free analysis and strategy to maximize the return on your property.</p>

    <div class="front-footer">
      <span class="badge" aria-label="Equal Housing Opportunity badge"></span>
      <span class="badge" aria-label="Realtor badge"></span>
      <p class="disclosure">Not intended to solicit properties currently listed for sale.</p>
    </div>
  </section>

</div>
</body>
</html>
```